KTWG application splash screen

We need a 1024x768 image for use as an application splash screen.
The image will be displayed full screen on an 10 inch industrial PC 1024x768 screen while our application is launching. The image should convey that the application is "Waiting for connection to Wi-Fi access point..." and include a graphic of the industrial PC connected to the access point via an Ethernet cable. A list of troubleshooting steps should be included at the bottom of the image. The troubleshooting steps should not be the main focus of the image and should be shown in a smaller font (but still readable at 1024x768 displayed on a 10 inch screen).
I will include a mock up of the general idea of what we are looking for as well as image files for the industrial PC, a screenshot of our application to show on the PC's screen and the AP.
For general look and feel and a sense of corporate branding please review our website https://marrowgatesoilworks.example/. The splash screen should reflect corporate branding.
Target Market(s)
Users of our application
Industry/Entity Type
Agriculture
Look and feel

```html
<!DOCTYPE html>
<html lang="en">
<head>
<meta charset="utf-8">
<title>KTWG – Waiting for Wi-Fi access point</title>
<link rel="stylesheet" href="https://fonts.googleapis.com/css2?family=Poppins:wght@400;500;600;700&display=swap">
<style>
  :root{
    --page:#f1f1f1;
    --card-top:#ffffff;
    --card-bottom:#dedede;
    --ink:#1d1d1d;
    --body:#3f3f3f;
    --green:#2bb463;
    --cable:#1a1a1a;
    --device:#2a2a2a;
    --ap:#f4f5f6;
  }
  *{margin:0;padding:0;box-sizing:border-box}
  html,body{width:1200px;height:1103px;overflow:hidden;background:var(--page);font-family:"Poppins",sans-serif}
  .splash{
    position:absolute;left:0;top:101px;width:1222px;height:917px;
    transform:scale(0.982);transform-origin:0 0;
    background:linear-gradient(135deg,var(--card-top) 0%,#f3f3f3 45%,var(--card-bottom) 100%);
    overflow:hidden;
  }
  .status-icon{position:absolute;left:572px;top:46px;width:108px;height:88px}
  .headline{
    position:absolute;left:0;width:100%;top:150px;text-align:center;
    font-weight:700;font-size:46px;line-height:56px;color:var(--ink);letter-spacing:-0.5px;
  }
  .device{
    position:absolute;left:126px;top:307px;width:345px;height:275px;
    border-radius:18px;background:linear-gradient(160deg,#3a3a3a,var(--device));
  }
  .access-point{
    position:absolute;left:1061px;top:302px;width:26px;height:226px;border-radius:8px;
    background:linear-gradient(90deg,#e3e5e7,var(--ap),#d9dbdd);
  }
  .link{position:absolute;left:0;top:0;width:1222px;height:917px}
  .label{position:absolute;font-weight:600;font-size:19px;color:var(--ink);letter-spacing:0.2px}
  .label-device{left:126px;width:345px;top:597px;text-align:center}
  .label-cable{left:514px;top:564px}
  .label-ap{left:780px;top:450px;line-height:25px}
  .label-ap .model{font-weight:400}
  .help-title{
    position:absolute;left:151px;top:658px;display:flex;align-items:center;gap:10px;
    color:var(--green);font-weight:600;font-size:21px;
  }
  .steps{position:absolute;left:163px;top:710px;list-style:none}
  .steps li{
    position:relative;padding-left:21px;font-size:15px;line-height:25px;color:var(--body);
  }
  .steps li::before{
    content:"";position:absolute;left:0;top:8px;width:10px;height:10px;border-radius:50%;background:var(--green);
  }
  .brand{
    position:absolute;left:1000px;top:812px;display:flex;align-items:center;gap:8px;
    font-weight:700;font-size:28px;color:var(--ink);letter-spacing:1px;
  }
  .brand-mark{width:12px;height:12px;background:var(--green)}
</style>
</head>
<body>
<main class="splash">
  <svg class="status-icon" viewBox="0 0 108 88" aria-hidden="true">
    <g fill="none" stroke="var(--green)" stroke-width="12" stroke-linecap="round">
      <path d="M8 36 C36 8 72 8 100 36"/>
      <path d="M26 54 C42 38 66 38 82 54"/>
    </g>
    <circle cx="54" cy="74" r="8" fill="var(--green)"/>
    <line x1="14" y1="6" x2="88" y2="82" stroke="#ffffff" stroke-width="20" stroke-linecap="round"/>
    <line x1="14" y1="6" x2="88" y2="82" stroke="var(--green)" stroke-width="10" stroke-linecap="round"/>
  </svg>

  <h1 class="headline">Waiting for connection to<br>Wi-Fi access point...</h1>

  <svg class="link" viewBox="0 0 1222 917" aria-hidden="true">
    <rect x="470" y="535" width="12" height="18" rx="2" fill="var(--cable)"/>
    <path d="M482 545 H1077 V529" fill="none" stroke="var(--cable)" stroke-width="4"/>
  </svg>

  <div class="device" role="img" aria-label="Rugged tractor cab computer showing the seeding application with green bar gauges"></div>
  <div class="access-point" role="img" aria-label="White outdoor Wi-Fi access point with two antennas"></div>

  <div class="label label-device">TRACTOR CAB COMPUTER</div>
  <div class="label label-cable">ETHERNET CABLE</div>
  <div class="label label-ap">WI-FI ACCESS POINT<br><span class="model">NORTHGATE AX-240 OUTDOOR</span></div>

  <h2 class="help-title">
    <svg width="32" height="34" viewBox="0 0 32 34" aria-hidden="true">
      <g fill="none" stroke="var(--green)" stroke-width="2">
        <circle cx="16" cy="13" r="10"/>
        <circle cx="16" cy="13" r="4"/>
        <path d="M4 30 L12 24 M28 30 L20 24 M6 32 H26"/>
      </g>
    </svg>
    Troubleshooting steps:
  </h2>

  <ul class="steps">
    <li>This screen should only be visible for a short time on boot.</li>
    <li>If this screen stays visible for more than a minute:</li>
    <li>Verify that the Wi-Fi Access Point (AP) powers up when this system does (indicated by a green light on the side of the AP).</li>
    <li>Check the Ethernet cable between this system and the AP for damage, and replace it if necessary.</li>
    <li>Power-cycle this system and wait for it to reboot fully.</li>
    <li>If the issue persists, contact KTWG support for further assistance.</li>
  </ul>

  <div class="brand"><span class="brand-mark"></span>KTWG</div>
</main>
</body>
</html>
```